Brindlewick Solutions Ltd

I'd like to create a company letterhead for the attached logo in word format.

I'd like to emphasis the icon in large translucent state from the left corner and ensure that the letterhead colouring matches the colour palette of the current logo with a contrast so it's clear to see. I've attached a copy of our sister company page on the app for reference.

```html
<!DOCTYPE html>
<html lang="en">
<head>
<meta charset="utf-8">
<title>Brindlewick Solutions Ltd – Letterhead</title>
<link rel="stylesheet" href="https://fonts.googleapis.com/css2?family=Montserrat:wght@400&family=Roboto:wght@400&display=swap">
<style>
  :root {
    --backdrop: #dcdcdc;
    --paper: #f7f7f7;
    --brand-teal: #1cb5a3;
    --brand-teal-faint: #e5f1f0;
    --footer-grey: #9a9a9a;
    --text-grey: #6f6f6f;
  }
  * { margin: 0; padding: 0; box-sizing: border-box; }
  html, body {
    width: 1153px; height: 1200px; overflow: hidden;
    background: var(--backdrop);
  }
  .letterhead {
    position: absolute; left: 160px; top: 20px;
    width: 832px; height: 1160px;
    background: var(--paper);
    overflow: hidden;
    box-shadow: 0 6px 24px rgba(0,0,0,0.12);
  }
  .watermark-ring {
    position: absolute; left: 0; top: 0;
    width: 832px; height: 1160px;
  }
  .brand {
    position: absolute; left: 73px; top: 92px;
    display: flex; align-items: center; gap: 12px;
  }
  .brand-dot {
    width: 34px; height: 34px; border-radius: 50%;
    background: var(--brand-teal);
  }
  .brand-name {
    font-family: "Montserrat", sans-serif; font-weight: 400;
    font-size: 22px; color: var(--brand-teal);
    line-height: 1.15;
  }
  .contact {
    position: absolute; left: 574px; top: 62px;
    font-family: "Roboto", sans-serif; font-size: 14.5px;
    color: var(--text-grey); line-height: 19px;
  }
  .contact-address { margin-bottom: 5px; }
  .contact-line { display: flex; align-items: center; gap: 5px; }
  .contact-icon { width: 13px; height: 13px; flex: none; }
  .footer-band {
    position: absolute; left: 0; bottom: 0;
    width: 832px; height: 17px;
  }
</style>
</head>
<body>
  <main class="letterhead">
    <svg class="watermark-ring" viewBox="0 0 832 1160" aria-hidden="true">
      <circle cx="196" cy="668" r="350" fill="none" stroke="var(--brand-teal-faint)" stroke-width="120"/>
    </svg>

    <div class="brand">
      <span class="brand-dot"></span>
      <span class="brand-name">Brindlewick<br>Solutions Ltd</span>
    </div>

    <address class="contact" style="font-style:normal">
      <div class="contact-address">48 Alder Crescent Suite 7<br>Fernhill, OR 97210</div>
      <div class="contact-line">
        <svg class="contact-icon" viewBox="0 0 16 16" aria-hidden="true"><path d="M2 5c0-1 1-2 6-2s6 1 6 2v1h-3V5H5v1H2z M4 7h8l1 6H3z" fill="var(--brand-teal)"/></svg>
        <span>1-800-555-0147</span>
      </div>
      <div class="contact-line">
        <svg class="contact-icon" viewBox="0 0 16 16" aria-hidden="true"><rect x="1" y="3" width="14" height="10" fill="var(--brand-teal)"/><path d="M1 3l7 6 7-6" fill="none" stroke="var(--paper)" stroke-width="1.3"/></svg>
        <span>hello@brindlewick.com</span>
      </div>
      <div class="contact-line">
        <svg class="contact-icon" viewBox="0 0 16 16" aria-hidden="true"><circle cx="8" cy="8" r="7" fill="var(--brand-teal)"/><path d="M8 1v14M1 8h14" stroke="var(--paper)" stroke-width="1"/></svg>
        <span>www.brindlewick.com</span>
      </div>
    </address>

    <svg class="footer-band" viewBox="0 0 832 17" aria-hidden="true">
      <polygon points="0,0 596,0 580,17 0,17" fill="var(--brand-teal)"/>
      <polygon points="602,0 832,0 832,17 586,17" fill="var(--footer-grey)"/>
    </svg>
  </main>
</body>
</html>
```